Bref créative
Business cards and stationary for mobile catering company
Harbour Spice
Bright & Fun-filled
Derek Tolman
Mobile Catering Proprietor
Fernleigh
Corbett Avenue
Borehamwood
Hertfordshire
WD4 7PQ
derek@harbourspice-example.co.uk
www.harbourspice-example.co.uk
we would like a simple but stylish desing in keeping with our logo
THIS IS OUR LOGO
the . eps file if required

```html
<!DOCTYPE html>
<html lang="en">
<head>
<meta charset="utf-8">
<title>Harbour Spice – Business Cards</title>
<link rel="stylesheet" href="https://fonts.googleapis.com/css2?family=Open+Sans:ital,wght@0,400;0,600;0,700;1,400&display=swap">
<style>
  :root {
    --page-bg: #ecebe7;
    --lime: #8dc63f;
    --lime-dark: #7cb532;
    --chili: #c8281e;
    --chili-dark: #9a1c14;
    --brown: #5b3a21;
    --white: #ffffff;
  }
  * { box-sizing: border-box; margin: 0; padding: 0; }
  html, body {
    width: 1200px; height: 989px; overflow: hidden;
    background: var(--page-bg);
    font-family: "Open Sans", Arial, sans-serif;
  }
  .canvas { position: relative; width: 1200px; height: 989px; }
  .card {
    position: absolute; left: 250px; width: 700px; height: 400px;
    overflow: hidden; border-radius: 4px;
    box-shadow: 0 6px 18px rgba(0,0,0,0.18);
  }
  /* back of card */
  .card-back { top: 60px; background: var(--lime); }
  .chili-art {
    position: absolute; left: 310px; top: 50px; width: 80px; height: 190px;
    border-radius: 6px;
    background: linear-gradient(180deg, var(--chili) 0%, var(--chili-dark) 100%);
  }
  .back-web {
    position: absolute; left: 0; right: 0; top: 300px;
    text-align: center; color: var(--white);
    font-size: 19px; font-weight: 600; letter-spacing: 3px;
  }
  /* front of card */
  .card-front { top: 520px; background: var(--white); }
  .brand {
    position: absolute; left: 0; right: 0; top: 62px;
    display: flex; align-items: center; justify-content: center; gap: 14px;
  }
  .brand-dot { width: 44px; height: 44px; border-radius: 50%; background: var(--brown); }
  .brand-name { font-size: 44px; font-weight: 600; color: var(--lime-dark); letter-spacing: -0.5px; }
  .brand-rule {
    position: absolute; left: 0; right: 0; top: 170px; height: 6px; background: var(--brown);
  }
  .info-band {
    position: absolute; left: 0; right: 0; top: 176px; bottom: 0;
    background: var(--lime); color: var(--white);
  }
  .person { position: absolute; left: 0; right: 0; top: 26px; text-align: center; }
  .person-name { font-size: 17px; font-weight: 700; }
  .person-role { font-size: 13px; font-style: italic; }
  .address {
    position: absolute; right: 362px; top: 98px; text-align: right;
    font-size: 12.5px; line-height: 19px; font-style: normal;
  }
  .divider {
    position: absolute; left: 350px; top: 100px; width: 1px; height: 78px; background: var(--white);
  }
  .contacts {
    position: absolute; left: 364px; top: 98px; list-style: none;
    font-size: 12.5px; line-height: 19px;
  }
  .contacts li { display: flex; align-items: center; gap: 7px; margin-bottom: 7px; }
  .contacts svg { width: 13px; height: 13px; flex: none; }
</style>
</head>
<body>
<main class="canvas">
  <section class="card card-back">
    <div class="chili-art" role="img" aria-label="Illustration of a red chilli pepper with a green stem"></div>
    <p class="back-web">www.harbourspice-example.co.uk</p>
  </section>

  <section class="card card-front">
    <div class="brand">
      <span class="brand-dot"></span>
      <span class="brand-name">Harbour Spice</span>
    </div>
    <div class="brand-rule"></div>
    <div class="info-band">
      <div class="person">
        <p class="person-name">Derek Tolman</p>
        <p class="person-role">Mobile Catering Proprietor</p>
      </div>
      <address class="address">
        Fernleigh, Corbett Avenue<br>
        Borehamwood Hertfordshire<br>
        WD4 7PQ
      </address>
      <div class="divider"></div>
      <ul class="contacts">
        <li>
          <svg viewBox="0 0 16 16" aria-hidden="true"><path fill="#fff" d="M3 1h3l1.5 4-2 1.3a9 9 0 0 0 4.2 4.2L11 8.5l4 1.5v3c0 1-1 2-2 2C6.5 15 1 9.5 1 3c0-1 1-2 2-2z"/></svg>
          07700 900418
        </li>
        <li>
          <svg viewBox="0 0 16 16" aria-hidden="true"><rect x="1" y="3" width="14" height="10" rx="1" fill="none" stroke="#fff" stroke-width="1.6"/><path d="M1.5 3.8 8 9l6.5-5.2" fill="none" stroke="#fff" stroke-width="1.6"/></svg>
          derek@harbourspice-example.co.uk
        </li>
        <li>
          <svg viewBox="0 0 16 16" aria-hidden="true"><circle cx="8" cy="8" r="6.5" fill="none" stroke="#fff" stroke-width="1.4"/><path d="M1.5 8h13M8 1.5c-3 3.5-3 9.5 0 13M8 1.5c3 3.5 3 9.5 0 13" fill="none" stroke="#fff" stroke-width="1.2"/></svg>
          www.harbourspice-example.co.uk
        </li>
      </ul>
    </div>
  </section>
</main>
</body>
</html>
```